Business Card for Multi-Brand Sportswear Company

We are looking for a business card which represents our company and the multiple brands within it.

The company: Fen Athletics (LTD)
The brands: Fen, TavaPuni, ElmStretch, Grit and Rain

Employees using these cards would be representing Fen Athletics, rather than any of the individual brands. You will see a current design within the uploaded files, to give some inspiration. The actual text of the brands is not necessary, but the logos should be on there is some format.

Our creative minds on this are stretched, so we are looking for someone to make this their own, and show us what a good business card should look like.

We may like to get these printed with spot gloss, so keep that in mind with your designs.

www.fenathletics.co.uk

Industry/Entity Type

Business

Contact Information for Business Card

Leo Pemberton-Hale
Operations Manager
(+44) 1632 960 418
Leo@fenathletics.co.uk
www.fenathletics.co.uk

Font styles to use
Sans Serif
Other font styles liked:
• Eurostile

Colors
ffffff

Requirements
Nice to have
• Dark (black) background

```html
<!DOCTYPE html>
<html lang="en">
<head>
<meta charset="utf-8">
<title>Fen Athletics – Business Card</title>
<link rel="stylesheet" href="https://fonts.googleapis.com/css2?family=Arimo:wght@400;700&family=Michroma&display=swap">
<style>
  :root {
    --canvas: #2b2725;
    --card-black: #161616;
    --card-black-soft: #1f1f1f;
    --back-mark: #262626;
    --red: #d7231d;
    --white: #ffffff;
    --grey-text: #d9d9d9;
  }
  html, body {
    margin: 0;
    padding: 0;
    width: 1200px;
    height: 716px;
    overflow: hidden;
    background: var(--canvas);
  }
  .canvas {
    position: relative;
    width: 1200px;
    height: 716px;
  }
  .card {
    position: absolute;
    top: 183px;
    width: 540px;
    height: 350px;
    background: var(--card-black);
    overflow: hidden;
    box-shadow: 0 10px 30px rgba(0,0,0,0.45);
  }
  .card--back { left: 40px; }
  .card--front {
    left: 620px;
    background: linear-gradient(160deg, var(--card-black-soft), var(--card-black));
  }

  /* Back face */
  .back-mark {
    position: absolute;
    left: 0; right: 0; top: 148px;
    text-align: center;
    font-family: "Michroma", sans-serif;
    font-size: 34px;
    letter-spacing: 1px;
    color: var(--back-mark);
  }

  /* Front face */
  .swoosh {
    position: absolute;
    inset: 0;
    width: 540px;
    height: 350px;
  }
  .holder {
    position: absolute;
    right: 20px;
    top: 84px;
    text-align: right;
    font-family: "Arimo", sans-serif;
    color: var(--white);
  }
  .holder__name {
    margin: 0;
    font-size: 18px;
    font-weight: 700;
  }
  .holder__role {
    margin: 3px 0 0;
    font-size: 13px;
  }
  .brand-name {
    position: absolute;
    left: 36px;
    top: 128px;
    font-family: "Michroma", sans-serif;
    font-size: 25px;
    color: var(--white);
    letter-spacing: 0.5px;
  }
  .contact {
    position: absolute;
    left: 36px;
    top: 176px;
    margin: 0;
    padding: 0;
    list-style: none;
    font-family: "Arimo", sans-serif;
    font-size: 13px;
    color: var(--grey-text);
  }
  .contact li {
    display: flex;
    align-items: center;
    gap: 8px;
    height: 19px;
  }
  .contact svg { width: 11px; height: 11px; flex: none; }
  .contact .accent { color: var(--red); }
  .contact__address { margin-top: 6px; }
  .brand-row {
    position: absolute;
    right: 22px;
    bottom: 22px;
    display: flex;
    gap: 14px;
    align-items: center;
    font-family: "Arimo", sans-serif;
    font-size: 10px;
    color: var(--white);
  }
  .brand-row span { display: flex; align-items: center; gap: 4px; }
  .brand-row i {
    display: inline-block;
    width: 7px; height: 7px;
    background: var(--red);
  }
</style>
</head>
<body>
<main class="canvas">

  <section class="card card--back" aria-label="Card back">
    <div class="back-mark">Fen Athletics</div>
  </section>

  <section class="card card--front" aria-label="Card front">
    <svg class="swoosh" viewBox="0 0 540 350" aria-hidden="true">
      <path fill="var(--red)" d="M20,0 L540,0 L540,255 C490,240 460,200 420,160 C380,120 330,90 20,0 Z"/>
      <path fill="none" stroke="var(--white)" stroke-width="9" transform="translate(-10,18)" d="M-40,-6 L20,0 C330,90 380,120 420,160 C460,200 490,240 560,262"/>
      <path fill="none" stroke="var(--white)" stroke-width="2" transform="translate(-20,38)" d="M-40,-6 L20,0 C330,90 380,120 420,160 C460,200 490,240 570,265"/>
    </svg>

    <div class="holder">
      <p class="holder__name">Leo Pemberton-Hale</p>
      <p class="holder__role">Operations Manager</p>
    </div>

    <div class="brand-name">Fen Athletics</div>

    <ul class="contact">
      <li>
        <svg viewBox="0 0 12 12"><path fill="var(--red)" d="M2,1 L5,1 L5,4 L3.5,5 C4,7 5,8 7,8.5 L8,7 L11,7 L11,10 C11,11 10,11 9,11 C5,11 1,7 1,3 C1,2 1,1 2,1 Z"/></svg>
        <span>+44 (0)1632 960418</span>
      </li>
      <li>
        <svg viewBox="0 0 12 12"><circle cx="6" cy="6" r="5" fill="none" stroke="var(--red)" stroke-width="1.4"/><path d="M1,6 H11 M6,1 C3,4 3,8 6,11 C9,8 9,4 6,1" fill="none" stroke="var(--red)" stroke-width="1"/></svg>
        <span>leo@fenathletics.co.uk</span>
      </li>
      <li>
        <svg viewBox="0 0 12 12"><rect x="1" y="2.5" width="10" height="7" fill="var(--red)"/><path d="M1,2.5 L6,7 L11,2.5" fill="none" stroke="var(--card-black)" stroke-width="1"/></svg>
        <span>www.<span class="accent">fenathletics</span>.co.uk</span>
      </li>
      <li class="contact__address">Reed Court, Ashby Marsh, Holme, YO9 4ZX</li>
    </ul>

    <div class="brand-row" aria-label="Group brands">
      <span><i></i>TavaPuni</span>
      <span>Grit and Rain</span>
      <span>Fen</span>
      <span>ElmStretch</span>
    </div>
  </section>

</main>
</body>
</html>
```